Graphic Design for a 3 Banner Tradeshow Setup

We are a Pipe Restoration company that specializes in trenchless pipelining. We need a design for a 3 banner setup to use at tradeshows. See attached "banner specs" for sizing - note the 48" x 92" will be in between the two 36" x 92" banners. See attached "Mock-Up" of information each banner needs and utilize the color scheme of the banners we already have in the "both DWM banners" AI file attached. The final designs should communicate what we do and attract people into our booth. We would like to have graphics of realistic pipes for a before (dirty pipe), after cleaning pipe, and lined pipe - see example of "pipe pictures" attached. I'm not sure if this is something you can generate or if we will need to find images of our own to send. Also, see attached "screenshot-process" to see similar images we would like to use to showcase the process.
Target Market(s)
Homeowners, Property Managers, HOA Communities, Healthcare Facilities & Hospitals, and commercial properties
Industry/Entity Type
Trenchless Pipelining
Look and feel

```html
<!DOCTYPE html>
<html lang="en">
<head>
<meta charset="utf-8">
<title>DWM Tradeshow Banners</title>
<link rel="stylesheet" href="https://fonts.googleapis.com/css2?family=Bebas+Neue&family=Montserrat:wght@500;600;700;800&family=Orbitron:wght@700&display=swap">
<style>
  :root{
    --navy:#0f1a2e;
    --navy-deep:#0b1426;
    --blue-dark:#2b2f7a;
    --blue-mid:#1566b0;
    --blue-bright:#00aee8;
    --white:#ffffff;
    --ink:#1a1f2b;
    --stage:#ececec;
    --disc:#e9e9ec;
  }
  *{margin:0;padding:0;box-sizing:border-box}
  html,body{width:1200px;height:720px;overflow:hidden;background:var(--stage)}
  .stage{position:relative;width:1200px;height:720px}
  .banner{position:absolute;top:44px;height:631px;overflow:hidden;background:var(--navy)}
  .banner--side-left{left:174px;width:247px}
  .banner--center{left:435px;width:330px}
  .banner--side-right{left:779px;width:247px}
  .banner svg.backdrop{position:absolute;inset:0}
  .brand{position:absolute;left:0;right:0;text-align:center;color:var(--white);font-family:"Montserrat",sans-serif;font-weight:800}
  .brand__name{display:block;letter-spacing:4px;line-height:1}
  .brand__tag{display:block;font-size:6px;letter-spacing:2.2px;margin-top:4px;font-weight:800}
  .banner--side-left .brand,.banner--side-right .brand{top:28px}
  .banner--side-left .brand__name,.banner--side-right .brand__name{font-size:30px}
  .banner--center .brand{top:30px}
  .banner--center .brand__name{font-size:38px}
  .banner--center .brand__tag{font-size:7.5px;letter-spacing:2.8px}
  .headline{position:absolute;left:0;right:0;text-align:center;color:var(--white);font-family:"Bebas Neue",sans-serif;line-height:.92}
  .banner--side-left .headline,.banner--side-right .headline{top:130px;font-size:52px}
  .banner--center .headline{top:130px;font-size:76px}
  .rule{position:absolute;left:50%;height:3px;background:var(--navy);transform:translateX(-50%);border-radius:2px}
  .service-grid{position:absolute;color:var(--white);font-family:"Montserrat",sans-serif;font-weight:600;font-size:11px;line-height:1.25}
  .service{position:absolute;width:90px}
  .service svg{display:block;width:36px;height:36px;margin-bottom:4px}
  .pitch{position:absolute;left:0;right:0;top:284px;text-align:center;color:var(--white);font-family:"Montserrat",sans-serif;font-weight:800;font-size:15px;line-height:1.38}
  .pipe-stage{position:absolute;border-radius:50%;background:var(--disc)}
  .pipe-label{position:absolute;font-family:"Montserrat",sans-serif;font-weight:600;font-size:11px;color:var(--ink);text-align:center;width:100px}
  .contact{position:absolute;left:0;right:0;text-align:center;color:var(--white)}
  .contact__phone{display:block;font-family:"Orbitron",sans-serif;font-weight:700}
  .contact__web{display:block;font-family:"Montserrat",sans-serif;font-weight:500}
  .banner--side-left .contact,.banner--side-right .contact{top:568px}
  .banner--side-left .contact__phone,.banner--side-right .contact__phone{font-size:17px}
  .banner--side-left .contact__web,.banner--side-right .contact__web{font-size:12px;letter-spacing:3px;margin-top:3px}
  .banner--center .contact{top:562px}
  .banner--center .contact__phone{font-size:23px}
  .banner--center .contact__web{font-size:17px;letter-spacing:4px;margin-top:2px}
</style>
</head>
<body>
<main class="stage">

  <!-- Assessment banner -->
  <section class="banner banner--side-left">
    <svg class="backdrop" width="247" height="631" viewBox="0 0 247 631">
      <defs>
        <linearGradient id="blueA" x1="0" y1="0" x2="1" y2="0.3">
          <stop offset="0" stop-color="var(--blue-dark)"/>
          <stop offset="0.5" stop-color="var(--blue-mid)"/>
          <stop offset="1" stop-color="var(--blue-bright)"/>
        </linearGradient>
        <linearGradient id="photoA" x1="0" y1="0" x2="1" y2="1">
          <stop offset="0" stop-color="#8a8378"/>
          <stop offset="0.5" stop-color="#5c5a5c"/>
          <stop offset="1" stop-color="#3f5a9a"/>
        </linearGradient>
      </defs>
      <rect x="0" y="330" width="247" height="230" fill="url(#photoA)" role="img" aria-label="Photo of a technician watching a pipe inspection camera monitor"/>
      <polygon points="30,378 120,430 215,372 215,378 120,438 30,384" fill="var(--white)"/>
      <polygon points="0,80 190,112 247,52 247,358 120,410 0,363" fill="url(#blueA)"/>
      <polygon points="0,77 190,98 247,48 247,54 190,115 0,82" fill="var(--white)"/>
      <rect x="0" y="560" width="247" height="71" fill="var(--navy)"/>
    </svg>
    <div class="brand"><span class="brand__name">DWM</span><span class="brand__tag">DRAIN WORKS METHODS</span></div>
    <h2 class="headline">WE ASSESS</h2>
    <div class="rule" style="top:179px;width:40px"></div>
    <div class="service-grid" style="left:0;top:0;width:247px;height:631px">
      <div class="service" style="left:24px;top:197px">
        <svg viewBox="0 0 36 36" fill="none" stroke="#fff" stroke-width="2.5"><path d="M2 4h32l-3 6H5z" fill="#fff"/><path d="M6 11q12 20 24 0"/><circle cx="18" cy="17" r="4"/></svg>
        CCTV Pipe<br>Investigation
      </div>
      <div class="service" style="left:145px;top:197px">
        <svg viewBox="0 0 36 36" fill="none" stroke="#fff" stroke-width="2.5"><circle cx="18" cy="18" r="11"/><path d="M18 2v10M18 24v10M2 18h10M24 18h10"/></svg>
        Scope<br>Development
      </div>
      <div class="service" style="left:24px;top:270px">
        <svg viewBox="0 0 36 36" fill="none" stroke="#fff" stroke-width="2"><rect x="6" y="4" width="18" height="26" rx="2"/><path d="M10 10h3v3h-3zM10 16h3v3h-3zM10 22h3v3h-3zM15 11h6M15 17h6"/><circle cx="26" cy="22" r="4" fill="#fff"/><path d="M19 34q7-9 14 0" fill="#fff"/></svg>
        Budgetary<br>Evaluation
      </div>
      <div class="service" style="left:145px;top:270px">
        <svg viewBox="0 0 36 36" fill="none" stroke="#fff" stroke-width="2.5"><circle cx="16" cy="16" r="13"/><path d="M6 16q10-10 20 0q-10 10-20 0z"/><circle cx="16" cy="16" r="3" fill="#fff"/><path d="M25 25l8 8"/></svg>
        Project<br>Oversight
      </div>
    </div>
    <div class="contact"><span class="contact__phone">1-800-555-0142</span><span class="contact__web">www.dwmlining.com</span></div>
  </section>

  <!-- Center banner -->
  <section class="banner banner--center">
    <svg class="backdrop" width="330" height="631" viewBox="0 0 330 631">
      <defs>
        <linearGradient id="blueC" x1="0" y1="0.2" x2="1" y2="0">
          <stop offset="0" stop-color="var(--blue-bright)"/>
          <stop offset="0.55" stop-color="var(--blue-mid)"/>
          <stop offset="1" stop-color="var(--blue-dark)"/>
        </linearGradient>
        <linearGradient id="accentC" x1="0" y1="0" x2="1" y2="0">
          <stop offset="0" stop-color="var(--blue-bright)"/>
          <stop offset="1" stop-color="var(--blue-dark)"/>
        </linearGradient>
      </defs>
      <rect x="0" y="0" width="330" height="631" fill="var(--white)"/>
      <rect x="0" y="0" width="330" height="80" fill="var(--navy)"/>
      <polygon points="0,55 75,112 330,78 330,352 166,384 0,352" fill="url(#blueC)"/>
      <polygon points="0,52 75,105 330,76 330,80 75,114 0,60" fill="var(--white)"/>
      <polygon points="36,366 130,398 160,400" fill="var(--navy)"/>
      <polygon points="294,366 200,398 175,400" fill="var(--navy)"/>
      <polygon points="40,550 220,518 310,555 220,534" fill="url(#accentC)"/>
      <polygon points="0,557 220,535 330,569 330,631 0,631" fill="var(--navy)"/>
    </svg>
    <div class="pipe-stage" role="img" aria-label="Cutaway rendering of a cleaned pipe with blue liner sliding in" style="left:123px;top:369px;width:90px;height:90px"></div>
    <div class="pipe-stage" role="img" aria-label="Cutaway rendering of a dirty pipe with rust and debris" style="left:24px;top:422px;width:78px;height:78px"></div>
    <div class="pipe-stage" role="img" aria-label="Cutaway rendering of a pipe with blue epoxy lining" style="left:234px;top:422px;width:78px;height:78px"></div>
    <div class="brand"><span class="brand__name">DWM</span><span class="brand__tag">DRAIN WORKS METHODS</span></div>
    <h1 class="headline">PIPE<br>PROBLEMS?</h1>
    <div class="rule" style="top:267px;width:52px"></div>
    <p class="pitch">WE HELP FIX PIPE PROBLEMS<br>WITHOUT HAVING TO TEAR UP<br>YOUR BUIDLING</p>
    <div class="pipe-label" style="left:121px;top:466px">Cleaned Pipe</div>
    <div class="pipe-label" style="left:13px;top:505px">Dirty Pipe</div>
    <div class="pipe-label" style="left:223px;top:505px">Lined Pipe</div>
    <div class="contact"><span class="contact__phone">1-800-555-0142</span><span class="contact__web">www.dwmlining.com</span></div>
  </section>

  <!-- Repair banner -->
  <section class="banner banner--side-right">
    <svg class="backdrop" width="247" height="631" viewBox="0 0 247 631">
      <defs>
        <linearGradient id="blueR" x1="0" y1="0" x2="1" y2="0.3">
          <stop offset="0" stop-color="var(--blue-dark)"/>
          <stop offset="0.5" stop-color="var(--blue-mid)"/>
          <stop offset="1" stop-color="var(--blue-bright)"/>
        </linearGradient>
        <linearGradient id="photoR" x1="0" y1="0" x2="1" y2="1">
          <stop offset="0" stop-color="#8a8378"/>
          <stop offset="0.5" stop-color="#5c5a5c"/>
          <stop offset="1" stop-color="#3f5a9a"/>
        </linearGradient>
      </defs>
      <rect x="0" y="330" width="247" height="230" fill="url(#photoR)" role="img" aria-label="Photo of a technician watching a pipe inspection camera monitor"/>
      <polygon points="34,378 126,432 215,372 215,378 126,440 34,384" fill="var(--white)"/>
      <polygon points="0,80 190,112 247,52 247,358 126,418 0,363" fill="url(#blueR)"/>
      <polygon points="0,77 190,98 247,48 247,54 190,115 0,82" fill="var(--white)"/>
      <rect x="0" y="560" width="247" height="71" fill="var(--navy)"/>
    </svg>
    <div class="brand"><span class="brand__name">DWM</span><span class="brand__tag">DRAIN WORKS METHODS</span></div>
    <h2 class="headline">WE FIX</h2>
    <div class="rule" style="top:179px;width:40px"></div>
    <div class="service-grid" style="left:0;top:0;width:247px;height:631px">
      <div class="service" style="left:25px;top:191px;width:70px">
        <svg viewBox="0 0 36 36" fill="none" stroke="#fff" stroke-width="2.5"><path d="M5 2v22q0 8 8 8t8-8v-8h10"/><circle cx="9" cy="27" r="2" fill="#fff"/><circle cx="15" cy="28" r="2" fill="#fff"/></svg>
        Slow<br>Drains
      </div>
      <div class="service" style="left:93px;top:191px;width:70px">
        <svg viewBox="0 0 36 36" fill="none" stroke="#fff" stroke-width="2.5"><path d="M6 18a13 13 0 1 0 4-9"/><path d="M2 12l4 6 5-5" fill="#fff"/><path d="M19 10v9l6 3"/></svg>
        Back-<br>Ups
      </div>
      <div class="service" style="left:168px;top:191px;width:75px">
        <svg viewBox="0 0 36 36" fill="none" stroke="#fff" stroke-width="2"><circle cx="24" cy="12" r="10"/><path d="M17 8h14M16 12h16M17 16h14M20 4v16M24 2v20M28 4v16"/><path d="M2 28q10-6 20-2v6H2z" fill="#fff"/></svg>
        Sewer<br>Odors
      </div>
      <div class="service" style="left:25px;top:275px;width:70px">
        <svg viewBox="0 0 36 36" fill="#fff"><path d="M6 2h12v12h12v14H18l-3 -6 3-4-4-3 3-4H10v-3z"/><path d="M8 28q-3 4 0 6t4-2l-2-4z"/></svg>
        Cracked<br>Pipes
      </div>
      <div class="service" style="left:93px;top:275px;width:75px">
        <svg viewBox="0 0 36 36" fill="none" stroke="#fff" stroke-width="2.2"><circle cx="17" cy="17" r="9"/><path d="M17 12v6M24 24l8 8"/><circle cx="17" cy="21.5" r="1" fill="#fff"/><path d="M17 2v4M4 8l3 2M30 8l-3 2M2 22h4"/></svg>
        Root<br>Intrusion
      </div>
      <div class="service" style="left:168px;top:275px;width:80px">
        <svg viewBox="0 0 36 36" fill="none" stroke="#fff" stroke-width="2"><path d="M8 8q0-6 8-6t8 6z" fill="#fff"/><circle cx="16" cy="13" r="5"/><path d="M2 34q0-12 14-12" fill="#fff"/><circle cx="27" cy="27" r="7"/><path d="M24 30l6-6"/></svg>
        Recurring<br>Plumbing<br>Problems
      </div>
    </div>
    <div class="contact"><span class="contact__phone">1-800-555-0142</span><span class="contact__web">www.dwmlining.com</span></div>
  </section>

</main>
</body>
</html>
```